Silver Harbor Staffing Agency

I need to make a brochure/catalogue that represent our company, telling our clients what we do, our values, fields of industry that we taken care of, so they know who we are, what we did, and how we do it.
I do have a logo and simple brochure design before that i really need to upgrade (i will give it as an example on this attachment).

What I want in the new design is :
1. More pictures and little bit of explanation in each industry we work with.
2. Attractive design that make people LOOK at the brochure and not just throw it in the trash.
3. Still use the combination color of the company logo itself, which is Golden Brown.

```html
<!DOCTYPE html>
<html lang="en">
<head>
<meta charset="utf-8">
<title>Silver Harbor Staffing Agency – Trifold Brochure</title>
<link href="https://fonts.googleapis.com/css2?family=Montserrat:wght@400;500;600;700;800&display=swap" rel="stylesheet">
<style>
:root{
  --gold:#b08d3a;
  --gold-light:#c9a24a;
  --ink:#1c1c1c;
  --paper:#ffffff;
  --bg:#ececec;
  --text-light:#e6e6e6;
  --text-dark:#3a3a3a;
  --map-tone:#e9e1cb;
}
*{box-sizing:border-box;margin:0;padding:0}
html,body{width:800px;height:1200px;overflow:hidden;background:var(--bg);font-family:'Montserrat',sans-serif}
.sheet{position:absolute;left:50px;width:700px;height:502px;background:var(--ink);overflow:hidden;box-shadow:0 6px 16px rgba(0,0,0,.25)}
.sheet--outside{top:60px}
.sheet--inside{top:632px}
.panel{position:absolute;top:0;width:233.33px;height:502px}
.p1{left:0}.p2{left:233.33px}.p3{left:466.66px}
.block{position:absolute;left:0;width:100%;padding:0 14px}
.heading{font-weight:700;font-size:10px;letter-spacing:.4px;color:var(--gold-light);text-transform:uppercase}
.heading u{text-decoration:none;border-bottom:1.5px solid currentColor;padding-bottom:1px}
.body{font-size:6.2px;line-height:1.35;color:var(--text-light);text-align:justify;margin-top:6px}
.dark .body{color:var(--text-dark)}
.photo{position:absolute}
.specialties{font-size:9.5px;line-height:1.3}
.spec-list{display:flex;margin-top:9px;font-size:6.5px;color:var(--text-light)}
.spec-list ul{list-style:none;width:50%}
.spec-list ul+ul{border-left:1px solid var(--gold);padding-left:14px}
.spec-list li{margin-bottom:7px;display:flex;align-items:center;gap:4px}
.tick{width:5px;height:5px;border:1px solid var(--gold-light);display:inline-block}
.brand{display:flex;align-items:center;gap:5px;font-weight:700;color:var(--gold-light);text-transform:uppercase;letter-spacing:.5px;white-space:nowrap}
.brand .mark{width:8px;height:8px;background:var(--gold-light)}
.contact-line{display:flex;align-items:flex-start;gap:5px;font-size:6.4px;color:var(--text-light);margin-top:5px}
.contact-line svg{flex:0 0 auto;margin-top:1px}
.phone-num{font-weight:700;font-size:9px}
.map-area{position:absolute;left:18px;top:44px;width:100px;height:166px;background:linear-gradient(180deg,var(--map-tone),#d8ccaa);border-radius:3px}
.states{position:absolute;left:128px;top:75px;font-size:6.2px;font-weight:700;color:#fff;line-height:1.35}
.cover-title{position:absolute;left:24px;top:360px;font-weight:700;font-size:21.5px;line-height:1.28;color:#fff;letter-spacing:1px}
.cover-title span{color:var(--gold-light)}
.cover-web{position:absolute;left:24px;top:470px;font-size:6.8px;color:#fff;letter-spacing:.3px}
.cover-web b{font-weight:700}
.tagline{position:absolute;left:0;width:100%;bottom:18px;text-align:center;font-weight:800;font-size:23px;letter-spacing:1px;color:#fff}
.tagline--gold{color:var(--gold-light)}
.industry{position:absolute;left:12px;width:209px;height:92px}
.industry h4{font-size:8px;font-weight:700;color:#fff;margin-bottom:3px}
.industry p{font-size:6.1px;line-height:1.33;color:var(--text-light);text-align:justify}
.industry .text{position:absolute;top:6px;width:118px}
.industry .pic{position:absolute;top:0;width:78px;height:88px;border:2px solid #fff}
.industry.right .text{left:0}.industry.right .pic{right:0}
.industry.left .text{right:0}.industry.left .pic{left:0}
.talent-band{position:absolute;left:0;bottom:0;width:100%;height:68px;background:var(--gold);text-align:center;padding-top:9px;font-weight:800;font-size:22px;line-height:1.05;color:var(--ink);letter-spacing:.8px}
</style>
</head>
<body>

<section class="sheet sheet--outside">
  <div class="panel p1">
    <div class="block" style="top:16px">
      <h3 class="heading"><u>Industries</u></h3>
      <p class="body">Need industry-leading talent for your organization? Career options that are ideal for your skills and experience? The professionals at Silver Harbor Staffing have the tools and knowledge to help you make the perfect match.</p>
    </div>
    <div class="photo" role="img" aria-label="Smiling housekeeper in a light blue uniform with a service cart in a hotel corridor" style="left:0;top:112px;width:233px;height:228px;background:linear-gradient(110deg,#c9d4e6 0%,#a9b8d2 40%,#a8643a 70%,#6a2f1c 100%)"></div>
    <div class="block" style="top:352px">
      <h3 class="heading specialties">Our Specialties<br>Include Staffing<br>for the Following<br>Industries</h3>
      <div class="spec-list">
        <ul>
          <li><i class="tick"></i>Warehousing</li>
          <li><i class="tick"></i>Hotel</li>
          <li><i class="tick"></i>Casino</li>
          <li><i class="tick"></i>Paper Mailing</li>
        </ul>
        <ul>
          <li><i class="tick"></i>Transportation</li>
          <li><i class="tick"></i>Landfill</li>
          <li><i class="tick"></i>Food Handling</li>
        </ul>
      </div>
    </div>
  </div>

  <div class="panel p2">
    <div class="block" style="top:16px">
      <h3 class="heading"><u>Contact Form</u></h3>
      <p class="body">Thank you for choosing Silver Harbor Staffing. If you have temporary jobs you are hiring for please get in touch with Northwind Enterprise Solutions. We are able to help with all your staffing and employment needs.</p>
    </div>
    <div style="position:absolute;left:0;top:112px;width:234px;height:228px;background:var(--gold)">
      <h3 class="heading" style="position:absolute;left:14px;top:16px;color:#fff"><u>Our Location</u></h3>
      <div class="map-area" role="img" aria-label="Outline map of the eastern United States with the served states marked"></div>
      <div class="states">New York<br>Pennsylvania<br>New Jersey<br>Delaware<br>Virginia</div>
    </div>
    <div class="block" style="top:356px">
      <div class="brand" style="font-size:7px"><i class="mark"></i>Silver Harbor Inc.</div>
      <h3 class="heading" style="margin-top:10px"><u>Contact Info</u></h3>
      <div class="contact-line"><svg width="8" height="8" viewBox="0 0 24 24"><path fill="#c9a24a" d="M6.6 10.8a15 15 0 0 0 6.6 6.6l2.2-2.2c.3-.3.7-.4 1-.2 1.1.4 2.3.6 3.6.6.6 0 1 .4 1 1V20c0 .6-.4 1-1 1A17 17 0 0 1 3 4c0-.6.4-1 1-1h3.5c.6 0 1 .4 1 1 0 1.3.2 2.5.6 3.6.1.3 0 .7-.2 1z"/></svg><span class="phone-num">555-014-2387</span></div>
      <div class="contact-line"><svg width="7" height="9" viewBox="0 0 24 30"><path fill="#c9a24a" d="M12 0a10 10 0 0 0-10 10c0 8 10 20 10 20s10-12 10-20A10 10 0 0 0 12 0zm0 14a4 4 0 1 1 0-8 4 4 0 0 1 0 8z"/></svg><span>48 Alder Lane, suite 210<br>Harbor Town, NJ 08000</span></div>
      <div class="contact-line"><svg width="8" height="7" viewBox="0 0 24 18"><rect width="24" height="18" rx="2" fill="#c9a24a"/><path d="M1 2l11 8 11-8" stroke="#1c1c1c" stroke-width="2" fill="none"/></svg><span>info@silverharborstaffing.com</span></div>
      <div class="contact-line"><svg width="8" height="8" viewBox="0 0 24 24"><circle cx="12" cy="12" r="10" fill="none" stroke="#c9a24a" stroke-width="2.5"/><path d="M2 12h20M12 2c4 4 4 16 0 20M12 2c-4 4-4 16 0 20" stroke="#c9a24a" stroke-width="2" fill="none"/></svg><span>www.silverharborstaffing.com</span></div>
    </div>
  </div>

  <div class="panel p3">
    <svg width="234" height="502" style="position:absolute;left:0;top:0">
      <polygon points="4,228 132,0 234,0 234,446" fill="#b08d3a"/>
    </svg>
    <div role="img" aria-label="Businessman with a briefcase climbing stairs toward a sunlit city skyline" style="position:absolute;left:0;top:0;width:234px;height:502px;background:linear-gradient(200deg,#e0a25a 0%,#9c9f9f 35%,#5b6d7a 75%,#3c4c5a 100%);clip-path:polygon(36px 228px,152px 0,234px 0,234px 420px)"></div>
    <div class="brand" style="position:absolute;left:14px;top:34px;font-size:6.8px"><i class="mark"></i>Silver Harbor Inc.</div>
    <h1 class="cover-title">YOUR<br>BEST WAY<br>TO <span>SUCCEED</span></h1>
    <p class="cover-web">www.<b>silverharborstaffing</b>.com</p>
  </div>
</section>

<section class="sheet sheet--inside">
  <div class="panel p1">
    <div class="block" style="top:16px">
      <h3 class="heading"><u>About Us</u></h3>
      <p class="body">With more than 18 years of experience Silver Harbor Staffing provided staffing services to a wide array of locations, all throughout Pennsylvania. Through the last few years we have expanded to 5 other states including New York, New Jersey, Delaware, Virginia and Georgia. Our ethics are a critical building block of our business. Our own success is based on adherence to the highest ethical standards, long-term client relationships, the ability to identify top candidates, and the high-quality professional development of Silver Harbor Staffing professionals protecting the confidentiality and interests of clients and candidates.</p>
    </div>
    <div class="block" style="top:180px;height:136px;background:var(--gold);padding-top:12px">
      <h3 class="heading" style="color:#fff"><u>Culture</u></h3>
      <p class="body" style="color:#fff">Silver Harbor Staffing believes in equal opportunity for all, regardless of gender, race, ethic, origin, religion, or handicap. The staffing policies and practices of Silver Harbor Staffing for our organization, our clients and candidates are fully non-discriminatory. Our employees are our most valuable asset. We strive to create a work environment of professionalism, trust and respect that will continuously provide our staff with motivation, challenge, and professional growth to aim our most important goal; CLIENT SATISFACTION.</p>
    </div>
    <div class="block" style="top:328px">
      <h3 class="heading"><u>Mission</u></h3>
      <p class="body">Silver Harbor Staffing is more than a staffing company; we want to become your business partner. We understand that payroll and employee-service overhead can be one of the largest expenses for your business. Through our partnership-network programs Silver Harbor Staffing can help you reduce the hard-costs of your business expenses. We take responsibility for all our placed employees, including payroll taxes and benefits allowing you to focus on running your business.</p>
    </div>
    <div class="tagline">CONNECTING</div>
  </div>

  <div class="panel p2 dark" style="background:var(--paper)">
    <div class="block" style="top:16px">
      <h3 class="heading" style="color:var(--gold)"><u>Our Process</u></h3>
      <p class="body">Our screening process includes a thorough interview with each potential candidate to give us insight into the candidate's previous work history, skills, communication abilities and career goals as well as reference checks with their previous employers.</p>
    </div>
    <div class="block" style="top:96px">
      <h3 class="heading" style="color:var(--gold)"><u>Our Services</u></h3>
      <p class="body">Silver Harbor Staffing's personalized services, expertise and affordable rates are key factors of our success and being our client's choice staffing agency. Our contingent and contract-to-hire employees are looking for flexible careers in New York, New Jersey, Pennsylvania, Delaware, Virginia and Georgia.</p>
    </div>
    <div class="photo" role="img" aria-label="Smiling manager with a clipboard in a warehouse aisle" style="left:0;top:180px;width:234px;height:136px;background:linear-gradient(100deg,#6b4a3a 0%,#c8cdd6 40%,#9aa7b8 60%,#a25a34 100%)"></div>
    <div class="block" style="top:328px">
      <h3 class="heading" style="color:var(--gold)"><u>Industries We Serve:</u></h3>
      <h4 style="font-size:8px;font-weight:700;color:var(--text-dark);margin-top:8px">Warehousing</h4>
      <p class="body" style="width:118px;margin-top:3px">Warehousing is the act of storing goods that will be sold or distributed later. While a small, home-based business might be warehousing products in a spare room, basement, or garage, larger businesses typically own or rent space in a building that is specifically designed for storage.</p>
      <div role="img" aria-label="Warehouse worker in a hard hat and safety vest" style="position:absolute;right:14px;top:28px;width:72px;height:80px;border:2px solid #1c1c1c;background:linear-gradient(160deg,#9aa7b0,#c8c84a 70%,#556070)"></div>
    </div>
    <div class="tagline tagline--gold">OPPORTUNITY</div>
  </div>

  <div class="panel p3">
    <div class="industry right" style="top:12px">
      <div class="text"><h4>Hotel</h4><p>Whether you are travelling for business or pleasure, the luxury hotel services offered by the five star Crescent Hall Hotel make it an ideal choice for your stay in Riga, Latvia.</p></div>
      <div class="pic" role="img" aria-label="Hotel housekeeper holding folded white towels" style="background:linear-gradient(160deg,#b9a38a,#efe9e0 60%,#8e7a66)"></div>
    </div>
    <div class="industry left" style="top:116px">
      <div class="pic" role="img" aria-label="Farm worker in a vest inside a barn" style="background:linear-gradient(160deg,#6d5a4a,#d9d4cc 50%,#8a2f2a)"></div>
      <div class="text" style="top:10px"><h4>Farming</h4><p>Farming is growing crops or keeping animals by people for food and raw materials. Farming is a part of agriculture.</p></div>
    </div>
    <div class="industry right" style="top:216px">
      <div class="text" style="top:14px"><h4>Paper Mailling</h4><p>Our paper mailing courier sacks have become popular with businesses and organisations looking for sustainable alternatives to polythene mailing bags.</p></div>
      <div class="pic" role="img" aria-label="Courier in a blue cap carrying a parcel and clipboard" style="background:linear-gradient(170deg,#ffffff 20%,#3a78c2 55%,#c9915a 75%,#ffffff)"></div>
    </div>
    <div class="industry left" style="top:318px">
      <div class="pic" role="img" aria-label="Worker in a yellow protective suit and mask outdoors" style="background:linear-gradient(160deg,#4c6a3a,#e2c92a 55%,#3e5a30)"></div>
      <div class="text" style="top:-2px"><h4>Landfill</h4><p>Landfill gas is produced by wet organic waste decomposing under anaerobic conditions in a landfill. Landfill gas production is dependant on the degradation status of the waste material as well as moisture and temperature, all of which may vary greatly.</p></div>
    </div>
    <div class="talent-band">WITH TODAY'S<br>TOP TALENT</div>
  </div>
</section>

</body>
</html>
```